New Business Card Design Project LORVANTI-Italy

we are LORVANTI-Italy
our company in the market for 3 years we are luxury cosmetic company and its about time for a facelift :)
i will like to have elegant luxurious and unique business card
that will give the person that get it a unique, luxurious and elegant impression
I'm VERY OPEN FOR NEW IDEAS , even duo i add a few files of things that i see on line and i like them

i add my logo as well
my website is LORVANTI.COM
(if you would like to see the main style that we have)

Target Market(s)

adult that have money :)

Industry/Entity Type

Business

Contact Information for Business Card

Name - Dario Lorvanti
Position - CEO and CO Founder
address - 4817 E Halvern
telephone - 555-384-1926
email - dario@lorvanti.com
fax - 555-384-1926
website - LORVANTI.COM

Colors
000000
959595
fbee3e
ffffff

Requirements
Must have
• big logo in GOLD color
• elegant look
• impressive
Nice to have
• not must but maybe classy pattern background
• not must but maybe emblem
• maybe clear plastic business card
Should not have
• colors
• images

```html
<!DOCTYPE html>
<html lang="en">
<head>
<meta charset="utf-8">
<title>LORVANTI-Italy Business Card</title>
<link rel="stylesheet" href="https://fonts.googleapis.com/css2?family=Crimson+Text:wght@400;600&display=swap">
<style>
  :root {
    --page-bg: #e7e4df;
    --card-dark-1: #3a3a3a;
    --card-dark-2: #111111;
    --gold: #c19a3f;
    --gold-deep: #9c7624;
    --gold-light: #dcb85e;
    --text-light: #f2f2f2;
    --frost-1: #f1ede8;
    --frost-2: #ddd6cd;
    --frost-edge: #c9c2b8;
  }
  * { box-sizing: border-box; margin: 0; padding: 0; }
  html, body { width: 1200px; height: 970px; overflow: hidden; }
  body {
    background: var(--page-bg);
    font-family: "Crimson Text", Georgia, serif;
    position: relative;
  }
  .business-card {
    position: absolute;
    left: 100px;
    top: 199px;
    width: 1000px;
    height: 572px;
    border-radius: 22px;
    overflow: hidden;
    display: flex;
    box-shadow: 0 12px 40px rgba(0,0,0,0.18);
  }
  .card-info {
    width: 489px;
    height: 100%;
    background: radial-gradient(ellipse at 20% 35%, var(--card-dark-1) 0%, #262626 45%, var(--card-dark-2) 100%);
    padding: 88px 0 0 70px;
    color: var(--text-light);
  }
  .person-name {
    font-size: 35px;
    font-weight: 600;
    color: var(--gold);
    line-height: 1.1;
  }
  .person-role {
    font-size: 25px;
    line-height: 1.3;
    margin-top: 2px;
  }
  .company-name {
    font-size: 25px;
    font-weight: 600;
    color: var(--gold);
    margin-top: 34px;
    line-height: 1.2;
  }
  .company-address {
    font-size: 25px;
    line-height: 1.3;
  }
  .contact-list {
    list-style: none;
    margin-top: 30px;
  }
  .contact-item {
    display: flex;
    align-items: center;
    font-size: 26px;
    line-height: 36.5px;
  }
  .contact-icon {
    width: 24px;
    height: 24px;
    margin-right: 14px;
    fill: var(--gold);
    flex-shrink: 0;
  }
  .contact-website { color: #e9d2c6; }
  .gold-border {
    width: 22px;
    height: 100%;
    background: linear-gradient(90deg, var(--gold-deep), var(--gold-light) 50%, var(--gold-deep));
  }
  .card-brand {
    flex: 1;
    height: 100%;
    background: linear-gradient(160deg, var(--frost-1) 0%, #e6e0d8 55%, var(--frost-2) 100%);
    position: relative;
  }
  .brand-mark {
    position: absolute;
    left: 0; right: 0;
    top: 124px;
    display: flex;
    flex-direction: column;
    align-items: center;
  }
  .brand-circle {
    width: 163px;
    height: 163px;
    border-radius: 50%;
    border: 5px solid var(--gold);
  }
  .brand-name {
    margin-top: 60px;
    font-size: 64px;
    font-weight: 400;
    letter-spacing: 2px;
    color: var(--gold);
    line-height: 1;
  }
</style>
</head>
<body>
  <div class="business-card">
    <section class="card-info">
      <h1 class="person-name">Dario Lorvanti</h1>
      <p class="person-role">CEO and CO Founder</p>
      <p class="company-name">LORVANTI-Italy</p>
      <p class="company-address">4817 E Halvern</p>
      <ul class="contact-list">
        <li class="contact-item">
          <svg class="contact-icon" viewBox="0 0 24 24" aria-hidden="true"><path d="M6.6 10.8c1.4 2.8 3.8 5.1 6.6 6.6l2.2-2.2c.3-.3.7-.4 1-.2 1.1.4 2.3.6 3.6.6.6 0 1 .4 1 1V20c0 .6-.4 1-1 1C10.6 21 3 13.4 3 4c0-.6.4-1 1-1h3.5c.6 0 1 .4 1 1 0 1.3.2 2.5.6 3.6.1.3 0 .7-.2 1z"/></svg>
          555-384-1926
        </li>
        <li class="contact-item">
          <svg class="contact-icon" viewBox="0 0 24 24" aria-hidden="true"><path d="M7 3h10v4H7zM4 8h16c1.1 0 2 .9 2 2v6h-4v4H6v-4H2v-6c0-1.1.9-2 2-2zm4 7v3h8v-3z"/></svg>
          555-384-1926
        </li>
        <li class="contact-item">
          <svg class="contact-icon" viewBox="0 0 24 24" aria-hidden="true"><path d="M2 6h20v12H2zm2 1.5v.4l8 5 8-5v-.4z"/></svg>
          dario@lorvanti.com
        </li>
        <li class="contact-item contact-website">
          <svg class="contact-icon" viewBox="0 0 24 24" aria-hidden="true"><path d="M12 2a10 10 0 1 0 0 20 10 10 0 0 0 0-20zm6.9 6h-2.9a15 15 0 0 0-1.3-3.7A8 8 0 0 1 18.9 8zM12 4c.8 1.1 1.5 2.5 1.9 4h-3.8c.4-1.5 1.1-2.9 1.9-4zM4.3 14a8 8 0 0 1 0-4h3.3a16 16 0 0 0 0 4zm.8 2h2.9c.3 1.3.8 2.6 1.3 3.7A8 8 0 0 1 5.1 16zM8 8H5.1a8 8 0 0 1 4.2-3.7C8.8 5.4 8.3 6.7 8 8zm4 12c-.8-1.1-1.5-2.5-1.9-4h3.8c-.4 1.5-1.1 2.9-1.9 4zm2.3-6H9.7a14 14 0 0 1 0-4h4.6a14 14 0 0 1 0 4zm.4 5.7c.5-1.1 1-2.4 1.3-3.7h2.9a8 8 0 0 1-4.2 3.7zm1.7-5.7a16 16 0 0 0 0-4h3.3a8 8 0 0 1 0 4z"/></svg>
          LORVANTI.COM
        </li>
      </ul>
    </section>
    <div class="gold-border" role="img" aria-label="Vertical gold ornamental border strip"></div>
    <section class="card-brand">
      <div class="brand-mark">
        <div class="brand-circle"></div>
        <p class="brand-name">LORVANTI</p>
      </div>
    </section>
  </div>
</body>
</html>
```